New business card/stationary for a consulting company

I am looking for a clean and very professional looking business card for my consulting company as well as corresponding stationary. I am uploading our logo. I like simple and powerful for the feel. No graphics but I am open on everything else. Below is my contact information but would like the final to be in a version I can add my employees information into and print. Thank you.

Daniel Whitcombe
dan@ferncliffadvisory.com
2870 North 9th Avenue, Summit Floor, Elm Ridge, Illinois 60531
www.ferncliffadvisory.com

Industry/Entity Type

Consulting

Contact Information for Business Card

Daniel Whitcombe
dan@ferncliffadvisory.com
www.ferncliffadvisory.com

Font styles to use
Serif
Sans Serif

Requirements
Must have
• Our logo and the business card details.
Nice to have
• our website www.ferncliffadvisory.com

```html
<!DOCTYPE html>
<html lang="en">
<head>
<meta charset="utf-8">
<title>Ferncliff Advisory – Business Cards</title>
<link rel="stylesheet" href="https://fonts.googleapis.com/css2?family=Montserrat:wght@300;400&family=Open+Sans:wght@400;700&display=swap">
<style>
  :root {
    --navy: #0c0a72;
    --navy-deep: #08065a;
    --paper: #ffffff;
    --backdrop: #2b2b2e;
    --white-soft: rgba(255,255,255,0.92);
  }
  * { box-sizing: border-box; margin: 0; padding: 0; }
  html, body {
    width: 1200px; height: 900px; overflow: hidden;
    background: var(--backdrop);
  }
  .canvas {
    position: relative; width: 1200px; height: 900px;
  }
  .card {
    position: absolute; left: 285px; width: 630px; height: 360px;
    box-shadow: 0 10px 30px rgba(0,0,0,0.45);
    overflow: hidden;
  }
  /* Back of card */
  .card-back {
    top: 70px;
    background: var(--navy);
    color: var(--white-soft);
    display: flex; flex-direction: column; align-items: center; justify-content: center;
  }
  .brand {
    display: flex; align-items: center; gap: 14px;
    font-family: "Montserrat", sans-serif; font-weight: 300;
    text-transform: uppercase; letter-spacing: 0.04em;
  }
  .brand-mark { display: block; flex: none; }
  .card-back .brand { font-size: 30px; color: var(--paper); }
  .card-back .brand-mark { width: 26px; height: 26px; background: var(--paper); }
  .card-back .website {
    margin-top: 46px;
    font-family: "Montserrat", sans-serif; font-weight: 300;
    font-size: 14px; letter-spacing: 0.42em; color: var(--paper);
  }
  /* Front of card */
  .card-front {
    top: 470px;
    background: var(--paper);
    display: flex;
  }
  .card-front .frame {
    position: absolute; inset: 14px;
    border: 2px solid var(--navy);
    pointer-events: none;
  }
  .contact-panel {
    position: relative; width: 44%; height: 100%;
    background: linear-gradient(160deg, var(--navy) 0%, var(--navy-deep) 100%);
    color: var(--paper);
    font-family: "Open Sans", sans-serif;
    padding: 96px 0 0 44px;
  }
  .contact-name {
    font-weight: 700; font-size: 19px; text-transform: uppercase;
    letter-spacing: 0.01em; margin-bottom: 16px;
  }
  .contact-address { font-size: 14px; line-height: 1.4; margin-bottom: 10px; }
  .contact-line {
    display: flex; align-items: center; gap: 9px;
    font-size: 14px; line-height: 1.5;
  }
  .contact-line svg { width: 12px; height: 12px; flex: none; }
  .brand-panel {
    position: relative; flex: 1;
    display: flex; align-items: center; justify-content: center;
    padding-bottom: 30px;
  }
  .brand-panel .brand { font-size: 19px; color: var(--navy); gap: 10px; }
  .brand-panel .brand-mark { width: 18px; height: 18px; background: var(--navy); }
</style>
</head>
<body>
<main class="canvas">

  <section class="card card-back" aria-label="Business card, back">
    <div class="brand">
      <span class="brand-mark"></span>
      <span class="brand-name">Ferncliff Advisory</span>
    </div>
    <p class="website">www.ferncliffadvisory.com</p>
  </section>

  <section class="card card-front" aria-label="Business card, front">
    <div class="contact-panel">
      <p class="contact-name">Daniel Whitcombe</p>
      <p class="contact-address">2870 North 9th Avenue<br>Summit Floor, Elm Ridge<br>Illinois 60531</p>
      <p class="contact-line">
        <svg viewBox="0 0 12 12" aria-hidden="true"><rect x="0.5" y="2" width="11" height="8" fill="#fff"/><path d="M0.5 2 L6 6.5 L11.5 2" fill="none" stroke="#0c0a72" stroke-width="1"/></svg>
        dan@ferncliffadvisory.com
      </p>
      <p class="contact-line">
        <svg viewBox="0 0 12 12" aria-hidden="true"><circle cx="6" cy="6" r="5.5" fill="#fff"/><path d="M0.5 6 H11.5 M6 0.5 C3 3.5 3 8.5 6 11.5 M6 0.5 C9 3.5 9 8.5 6 11.5" fill="none" stroke="#0c0a72" stroke-width="0.9"/></svg>
        www.ferncliffadvisory.com
      </p>
    </div>
    <div class="brand-panel">
      <div class="brand">
        <span class="brand-mark"></span>
        <span class="brand-name">Ferncliff Advisory</span>
      </div>
    </div>
    <div class="frame"></div>
  </section>

</main>
</body>
</html>
```